Website for Ashcombe Tube Drift

Require a website for a river float in the City of Edmonton. Located on North Saskatchewan River. Will need to be a coded website with incorporated booking system through Fare Harbor software.

Pages include
Home
Pricing
About
FAQ
Contact

Ashcombe Tube Drift is an activity based business that will have customers floating down the North Saskatchewan river in Edmonton AB. The site will have all information needed and a full reservation system. The project was launched to provide people in the Edmonton area a favorite summer activity.

Here are similar websites to reference what our business will be doing and what we are looking for.

mossbankfloatco.com
quillpointpaddles.com

Target Market(s)

Families, Groups, Individuals, Anyone who wants to explore the river

Industry/Entity Type

Activities based business/ Outdoor recreational/ River Float

Coding

Coded - Design and coding required

Number of Pages Required

5+ page

Colors
0054AA
0677BA
7BADD7
CADEEF
E8F1F8
F0912C
F2A743
F7CA91
FBE8D2
FDF5EE

```html
<!DOCTYPE html>
<html lang="en">
<head>
<meta charset="utf-8">
<title>Ashcombe Tube Drift</title>
<link rel="stylesheet" href="https://fonts.googleapis.com/css2?family=Hind:wght@400;500;600;700&family=Lato:wght@400;700;900&family=Montserrat:wght@400;500;600&display=swap">
<style>
:root{
  --navy:#042c5e;
  --title:#0e3572;
  --deep:#0054AA;
  --sky:#4cc4ea;
  --orange:#e2592b;
  --ink:#1d1d1d;
  --grey:#4a4a4a;
  --row:#f6f6f6;
  --row-num:#ededed;
  --white:#ffffff;
  --black:#000000;
}
*{box-sizing:border-box;margin:0;padding:0}
html,body{width:1200px;height:3245px;overflow:hidden}
body{position:relative;background:var(--white);font-family:'Lato',sans-serif;color:var(--ink)}
.abs{position:absolute}
.btn{position:absolute;display:flex;align-items:center;justify-content:center;background:var(--orange);color:var(--white);font-family:'Lato',sans-serif;font-weight:900;font-size:14px;border-radius:24px;letter-spacing:.2px}

/* top bar */
.topbar{position:absolute;left:0;top:0;width:1200px;height:68px;background:var(--navy);color:var(--white);font-size:15px}
.topbar .item{position:absolute;top:24px;display:flex;align-items:center;gap:12px}
.social-ring{position:absolute;top:14px;width:41px;height:41px;border:1.5px solid var(--white);border-radius:50%;display:flex;align-items:center;justify-content:center}
.divider-v{position:absolute;left:969px;top:27px;width:1px;height:15px;background:#8a9bb4}

/* nav */
.nav{position:absolute;left:0;top:68px;width:1200px;height:89px;background:var(--white);font-size:16px;font-weight:500}
.nav a{position:absolute;top:36px;color:var(--ink);text-decoration:none}
.nav a.active{color:var(--sky)}
.brand-badge{position:absolute;left:502px;top:16px;width:196px;height:196px;border-radius:50%;background:var(--white);display:flex;align-items:center;justify-content:center;text-align:center;font-family:'Hind',sans-serif;font-weight:700;color:var(--title);font-size:25px;line-height:1.05;z-index:3}

/* hero */
.hero{position:absolute;left:0;top:157px;width:1200px;height:660px;background:linear-gradient(180deg,#b9a88c 0%,#c9b190 25%,#8a8f86 45%,#3d5a3a 62%,#4c6b61 75%,#2f4a2c 100%)}
.hero-text{position:absolute;left:0;width:1200px;text-align:center}
.welcome{top:113px;font-size:40px;color:var(--white);letter-spacing:1px}
.hero-title{top:172px;font-family:'Hind',sans-serif;font-weight:700;font-size:62px;color:var(--title);letter-spacing:1.5px}
.hero-sub{top:254px;font-size:25px;color:var(--white)}
.dot{position:absolute;top:677px;width:10px;height:10px;border-radius:50%;background:var(--white)}

/* pricing */
.pricing-photo{position:absolute;left:111px;top:881px;width:489px;height:393px;border-radius:38px;background:linear-gradient(135deg,#efe1b6 0%,#c9a45c 30%,#5d6a3c 60%,#2f3a22 100%)}
.section-h{font-family:'Hind',sans-serif;font-weight:600;color:var(--ink)}
.tick-row{position:absolute;display:flex;font-size:12.5px;color:var(--ink)}
.tick{display:flex;align-items:center;gap:6px;margin-right:18px}
.link-book{color:var(--orange);font-weight:700;font-size:14px;text-decoration:underline}

/* about */
.about{position:absolute;left:0;top:1401px;width:1200px;height:522px;background:linear-gradient(120deg,#14396f 0%,#1d4b84 40%,#163e74 70%,#0f3366 100%)}
.about h2{position:absolute;left:111px;top:90px;font-family:'Hind',sans-serif;font-weight:700;font-size:29px;color:var(--white)}
.about p{position:absolute;left:111px;top:152px;width:489px;font-size:15px;line-height:25.8px;color:var(--white);text-align:justify}
.about-ring{position:absolute;left:663px;top:100px;width:330px;height:330px;border-radius:50%;border:8px solid var(--sky);background:linear-gradient(180deg,#3f5c2e 0%,#5b7a3e 45%,#6d7f6a 62%,#4c5e52 100%)}

/* faq */
.faq-title{position:absolute;left:0;top:2003px;width:1200px;text-align:center;font-family:'Hind',sans-serif;font-weight:600;font-size:29px;letter-spacing:1px;color:var(--ink)}
.faq-row{position:absolute;left:111px;width:977px;background:var(--row);font-family:'Montserrat',sans-serif}
.faq-num{position:absolute;left:0;top:0;width:70px;height:100%;background:var(--row-num);font-size:18px;font-weight:500;color:var(--ink);text-align:center;padding-top:20px}
.faq-q{position:absolute;left:103px;top:19px;font-size:17px;color:var(--grey);letter-spacing:.3px}
.faq-sign{position:absolute;right:26px;top:17px;font-size:17px;font-weight:600;color:var(--grey)}
.faq-open .faq-q{color:var(--title);font-weight:500}
.faq-a{position:absolute;left:103px;top:68px;width:800px;font-family:'Lato',sans-serif;font-size:14.5px;line-height:25.5px;color:#666}

/* footer */
.footer{position:absolute;left:0;top:2740px;width:1200px;height:505px;background:var(--black)}
.foot-contact{position:absolute;display:flex;align-items:center;gap:14px}
.foot-label{font-family:'Montserrat',sans-serif;font-size:12px;color:var(--orange);font-weight:500}
.foot-val{font-family:'Montserrat',sans-serif;font-size:15px;color:var(--white);margin-top:3px}
.foot-h{position:absolute;font-family:'Hind',sans-serif;font-weight:700;font-size:21px;color:var(--white);line-height:34px}
.foot-links{position:absolute;left:321px;top:2963px;font-family:'Montserrat',sans-serif;font-size:15px;color:var(--white);line-height:26px;list-style:none}
.map{position:absolute;left:502px;top:2999px;width:253px;height:146px;border-radius:6px;background:linear-gradient(135deg,#e8efe9 0%,#cfe1d3 45%,#b9d6c3 100%)}
.news-input{position:absolute;left:831px;top:3052px;width:257px;height:43px;border-radius:4px;overflow:hidden;background:var(--white);display:flex}
.news-input .ph{flex:1;font-family:'Montserrat',sans-serif;font-size:12px;color:#333;padding:15px 0 0 12px}
.news-input .send{width:86px;background:var(--orange);color:var(--white);font-weight:700;font-size:15px;display:flex;align-items:center;justify-content:center;font-family:'Montserrat',sans-serif}
.foot-social{position:absolute;top:3055px;width:36px;height:36px;border-radius:50%;background:var(--white);display:flex;align-items:center;justify-content:center}
.copyright{position:absolute;left:0;top:3184px;width:1200px;text-align:center;font-size:15px;color:var(--white)}
</style>
</head>
<body>

<header class="topbar">
  <div class="item" style="left:113px">
    <svg width="18" height="18" viewBox="0 0 24 24"><path fill="#4cc4ea" d="M6.6 10.8a15.1 15.1 0 0 0 6.6 6.6l2.2-2.2c.3-.3.7-.4 1-.2 1.1.4 2.3.6 3.6.6.6 0 1 .4 1 1V20c0 .6-.4 1-1 1A17 17 0 0 1 3 4c0-.6.4-1 1-1h3.5c.6 0 1 .4 1 1 0 1.3.2 2.5.6 3.6.1.3 0 .7-.2 1z"/></svg>
    <span>+1 (555) 014 2290</span>
  </div>
  <div class="item" style="left:714px">
    <svg width="18" height="14" viewBox="0 0 24 18"><rect width="24" height="18" rx="2" fill="#4cc4ea"/><path d="M1 2l11 8 11-8" stroke="#042c5e" stroke-width="2" fill="none"/></svg>
    <span>info@ashcombetubedrift.com</span>
  </div>
  <div class="divider-v"></div>
  <div class="social-ring" style="left:992px" aria-label="Share">
    <svg width="16" height="16" viewBox="0 0 24 24"><circle cx="18" cy="5" r="3" fill="#fff"/><circle cx="6" cy="12" r="3" fill="#fff"/><circle cx="18" cy="19" r="3" fill="#fff"/><path d="M8.6 10.5l6.8-4M8.6 13.5l6.8 4" stroke="#fff" stroke-width="2"/></svg>
  </div>
  <div class="social-ring" style="left:1046px" aria-label="Link">
    <svg width="16" height="16" viewBox="0 0 24 24"><path d="M10 14a5 5 0 0 0 7 0l3-3a5 5 0 0 0-7-7l-1 1M14 10a5 5 0 0 0-7 0l-3 3a5 5 0 0 0 7 7l1-1" stroke="#fff" stroke-width="2.2" fill="none" stroke-linecap="round"/></svg>
  </div>
</header>

<nav class="nav">
  <a class="active" style="left:112px">HOME</a>
  <a style="left:195px">PRICING</a>
  <a style="left:293px">ABOUT</a>
  <a style="left:383px">FAQ</a>
  <a style="left:784px">CONTACT US</a>
  <svg class="abs" style="left:911px;top:36px" width="17" height="17" viewBox="0 0 24 24"><circle cx="10" cy="10" r="7" stroke="#4cc4ea" stroke-width="3" fill="none"/><path d="M15 15l6 6" stroke="#4cc4ea" stroke-width="3"/></svg>
  <div class="btn" style="left:957px;top:22px;width:131px;height:45px">BOOK NOW</div>
</nav>
<div class="brand-badge">Ashcombe<br>Tube Drift</div>

<section class="hero" role="img" aria-label="Downtown Edmonton skyline at sunset above the river, bridge and green riverbank">
  <div class="hero-text welcome">WELCOME TO</div>
  <div class="hero-text hero-title">ASHCOMBE TUBE DRIFT</div>
  <div class="hero-text hero-sub">Float the North Saskatchewan through downtown Edmonton</div>
  <div class="btn" style="left:534px;top:308px;width:131px;height:45px">BOOK NOW</div>
</section>
<div class="dot" style="left:578px"></div>
<div class="abs" style="left:593px;top:674px;width:16px;height:16px;border-radius:50%;background:var(--orange);border:3px solid var(--white)"></div>
<div class="dot" style="left:613px"></div>
<svg class="abs" style="left:0;top:700px" width="1200" height="120" viewBox="0 0 1200 120">
  <path d="M0 18 C120 70 220 106 315 106 C440 106 500 11 604 11 C720 11 800 106 906 106 C1010 106 1100 60 1200 18 L1200 120 L0 120Z" fill="#4cc4ea"/>
  <path d="M0 34 C120 82 220 118 315 118 C440 118 500 27 604 27 C720 27 800 118 906 118 C1010 118 1100 74 1200 34 L1200 120 L0 120Z" fill="#ffffff"/>
</svg>

<div class="pricing-photo" role="img" aria-label="Two paddlers in life jackets on a sunlit river"></div>
<section>
  <h2 class="abs section-h" style="left:647px;top:874px;font-size:29px">OUR PRICING</h2>
  <h3 class="abs section-h" style="left:647px;top:937px;font-size:25px;font-weight:500">Tube and Shuttle</h3>
  <div class="abs" style="left:647px;top:980px;font-family:'Hind',sans-serif">
    <span style="font-size:38px;color:var(--sky);font-weight:500">$30</span><span style="font-size:22px;font-weight:500">/person</span>
  </div>
  <span class="abs link-book" style="left:797px;top:990px">BOOK NOW</span>
  <p class="abs" style="left:648px;top:1037px;width:460px;font-size:15px;line-height:26px">We keep our pricing simple and include everything you need: Premium comfort float tube with backrest and cup holder</p>
  <div class="tick-row" style="left:648px;top:1105px">
    <span class="tick"><svg width="12" height="10" viewBox="0 0 12 10"><path d="M1 5l3.5 3.5L11 1" stroke="#4cc4ea" stroke-width="2" fill="none"/></svg>Lifejacket</span>
    <span class="tick"><svg width="12" height="10" viewBox="0 0 12 10"><path d="M1 5l3.5 3.5L11 1" stroke="#4cc4ea" stroke-width="2" fill="none"/></svg>Paddle</span>
    <span class="tick"><svg width="12" height="10" viewBox="0 0 12 10"><path d="M1 5l3.5 3.5L11 1" stroke="#4cc4ea" stroke-width="2" fill="none"/></svg>Round trip shuttle</span>
    <span class="tick"><svg width="12" height="10" viewBox="0 0 12 10"><path d="M1 5l3.5 3.5L11 1" stroke="#4cc4ea" stroke-width="2" fill="none"/></svg>Safety training</span>
  </div>
  <div class="tick-row" style="left:648px;top:1148px">
    <span class="tick"><svg width="12" height="10" viewBox="0 0 12 10"><path d="M1 5l3.5 3.5L11 1" stroke="#4cc4ea" stroke-width="2" fill="none"/></svg>Staff assistance</span>
    <span class="tick"><svg width="12" height="10" viewBox="0 0 12 10"><path d="M1 5l3.5 3.5L11 1" stroke="#4cc4ea" stroke-width="2" fill="none"/></svg>Parking</span>
    <span class="tick"><svg width="12" height="10" viewBox="0 0 12 10"><path d="M1 5l3.5 3.5L11 1" stroke="#4cc4ea" stroke-width="2" fill="none"/></svg>Unlimited Fun!</span>
  </div>
  <span class="abs link-book" style="left:970px;top:1142px">BOOK NOW</span>
  <h3 class="abs section-h" style="left:648px;top:1189px;font-size:21px;font-weight:500">Group of 10 or more?</h3>
  <p class="abs" style="left:649px;top:1227px;font-size:14px">*does not include taxes or fees</p>
  <div class="btn" style="left:647px;top:1270px;width:131px;height:46px">CONTACT US</div>
</section>

<section class="about" role="img" aria-label="Kayakers on the river behind a navy overlay">
  <h2>ABOUT US</h2>
  <p>Float the North Saskatchewan through downtown Edmonton Edmonton's Best Summer Activity We provide the lifejacket, paddle, river tube and shuttle service. You just have to show up. Ashcombe Tube Drift was launched to provide people in the Edmonton area a favorite summeractivity. Nothing is better on a hot summer day, than spending it on the river and seeing Edmonton from a new perspective.Our home base and meeting spot is at Willowbend Landing (Map Link), by the Larkhill Glasshouse.</p>
  <div class="btn" style="left:111px;top:389px;width:131px;height:46px">BOOK NOW</div>
  <div class="about-ring" role="img" aria-label="Group of people floating on colourful tubes beside a wooded bank"></div>
</section>

<h2 class="faq-title">FREQUENTLY ASKED QUESTIONS</h2>
<div class="faq-row" style="top:2086px;height:63px"><div class="faq-num">1</div><div class="faq-q">How do I reserve my float?</div><div class="faq-sign">+</div></div>
<div class="faq-row faq-open" style="top:2156px;height:148px"><div class="faq-num">2</div><div class="faq-q">What safety information should I know?</div><div class="faq-sign">−</div>
  <div class="faq-a">Children 12 years and younger should be accompanied by an adult at all times on the river.Life jackets and paddles are provided and are recommended for everyone, especially if you are a weak or inexperienced swimmer.</div></div>
<div class="faq-row" style="top:2309px;height:63px"><div class="faq-num">3</div><div class="faq-q">What is included?</div><div class="faq-sign">+</div></div>
<div class="faq-row" style="top:2377px;height:63px"><div class="faq-num">4</div><div class="faq-q">What should I bring?</div><div class="faq-sign">+</div></div>
<div class="faq-row" style="top:2446px;height:63px"><div class="faq-num">5</div><div class="faq-q">Where are you located?</div><div class="faq-sign">+</div></div>
<div class="btn" style="left:530px;top:2537px;width:140px;height:46px">LOAD MORE</div>

<svg class="abs" style="left:0;top:2620px" width="1200" height="130" viewBox="0 0 1200 130">
  <path d="M0 88 C110 40 210 12 320 12 C440 12 500 95 600 95 C720 95 790 12 900 12 C1010 12 1100 40 1200 88 L1200 130 L0 130Z" fill="#4cc4ea"/>
  <path d="M0 104 C110 54 210 28 320 28 C440 28 500 111 600 111 C720 111 790 28 900 28 C1010 28 1100 54 1200 104 L1200 130 L0 130Z" fill="#000000"/>
</svg>
<footer class="footer"></footer>

<div class="foot-contact" style="left:111px;top:2793px">
  <svg width="28" height="28" viewBox="0 0 24 24"><path fill="#e2592b" d="M6.6 10.8a15.1 15.1 0 0 0 6.6 6.6l2.2-2.2c.3-.3.7-.4 1-.2 1.1.4 2.3.6 3.6.6.6 0 1 .4 1 1V20c0 .6-.4 1-1 1A17 17 0 0 1 3 4c0-.6.4-1 1-1h3.5c.6 0 1 .4 1 1 0 1.3.2 2.5.6 3.6.1.3 0 .7-.2 1z"/></svg>
  <div><div class="foot-label">Give Us A Call</div><div class="foot-val">+1 (555) 014 2290</div></div>
</div>
<div class="abs" style="left:364px;top:2785px;width:1px;height:70px;background:#333"></div>
<div class="foot-contact" style="left:434px;top:2791px">
  <svg width="28" height="20" viewBox="0 0 24 18"><rect width="24" height="18" rx="2" fill="#e2592b"/><path d="M1 2l11 8 11-8" stroke="#000" stroke-width="2" fill="none"/></svg>
  <div><div class="foot-label">Address</div><div class="foot-val">2150 Riverbend Rd NW, Edmonton, AB</div></div>
</div>
<div class="abs" style="left:782px;top:2785px;width:1px;height:70px;background:#333"></div>
<div class="foot-contact" style="left:835px;top:2793px">
  <svg width="28" height="20" viewBox="0 0 24 18"><rect width="24" height="18" rx="2" fill="#e2592b"/><path d="M1 2l11 8 11-8" stroke="#000" stroke-width="2" fill="none"/></svg>
  <div><div class="foot-label">Email Address</div><div class="foot-val">info@ashcombetubedrift.com</div></div>
</div>
<div class="abs" style="left:111px;top:2871px;width:977px;height:1px;background:#333"></div>

<div class="abs" style="left:111px;top:2915px;width:150px;font-family:'Hind',sans-serif;font-weight:700;font-size:27px;line-height:1.05;color:var(--sky)">Ashcombe<br>Tube Drift</div>
<div class="foot-social" style="left:112px" aria-label="Share">
  <svg width="15" height="15" viewBox="0 0 24 24"><circle cx="18" cy="5" r="3" fill="#042c5e"/><circle cx="6" cy="12" r="3" fill="#042c5e"/><circle cx="18" cy="19" r="3" fill="#042c5e"/><path d="M8.6 10.5l6.8-4M8.6 13.5l6.8 4" stroke="#042c5e" stroke-width="2"/></svg>
</div>
<div class="foot-social" style="left:155px" aria-label="Link">
  <svg width="15" height="15" viewBox="0 0 24 24"><path d="M10 14a5 5 0 0 0 7 0l3-3a5 5 0 0 0-7-7l-1 1M14 10a5 5 0 0 0-7 0l-3 3a5 5 0 0 0 7 7l1-1" stroke="#042c5e" stroke-width="2.4" fill="none" stroke-linecap="round"/></svg>
</div>
<div class="foot-social" style="left:198px" aria-label="Email">
  <svg width="15" height="12" viewBox="0 0 24 18"><rect x="1" y="1" width="22" height="16" rx="2" stroke="#042c5e" stroke-width="2" fill="none"/><path d="M2 3l10 7 10-7" stroke="#042c5e" stroke-width="2" fill="none"/></svg>
</div>
<div class="foot-social" style="left:241px" aria-label="Call">
  <svg width="15" height="15" viewBox="0 0 24 24"><path fill="#042c5e" d="M6.6 10.8a15.1 15.1 0 0 0 6.6 6.6l2.2-2.2c.3-.3.7-.4 1-.2 1.1.4 2.3.6 3.6.6.6 0 1 .4 1 1V20c0 .6-.4 1-1 1A17 17 0 0 1 3 4c0-.6.4-1 1-1h3.5c.6 0 1 .4 1 1 0 1.3.2 2.5.6 3.6.1.3 0 .7-.2 1z"/></svg>
</div>

<h3 class="foot-h" style="left:321px;top:2911px">QUICK LINKS</h3>
<ul class="foot-links">
  <li>Home</li><li>Pricing</li><li>About</li><li>Faq</li><li>Contact</li>
</ul>

<h3 class="foot-h" style="left:502px;top:2911px">COME VISIT US ON<br>FLOAT DAYS</h3>
<div class="map" role="img" aria-label="Map showing the meeting spot by the river"></div>

<h3 class="foot-h" style="left:831px;top:2911px">NEWSLETTER</h3>
<p class="abs" style="left:831px;top:2965px;font-family:'Montserrat',sans-serif;font-size:15px;line-height:26px;color:var(--white)">Lorem ipsum dolor sit amet,<br>adipisci elit, sed do eiusmod</p>
<div class="news-input"><span class="ph">Your email address</span><span class="send">SEND</span></div>

<p class="copyright">©Copyrights 2022 Ashcombetubedrift &nbsp;| &nbsp;&nbsp;All Rights Reserved</p>

</body>
</html>
```